Bluefinch Painting needs a Website

We need a website built for a Painting company I own, we mainly do residential painting, but don't want to be limited to that.

Need to have estimate request form.
Need pic's of past projects

I like the look of the website for http://www.harbor-brushworks.com
& "Westlake Home inspections"

My logo that was designed here on ArtHatch on the front page

I would like one of the houses I downloaded as part of the background
of the front page.

Target Market(s)

Home owners

Industry/Entity Type

Painting

Number of Pages Required

1 page

Font styles to use
Serif

Requirements
Must have
• Estimate request form for home owners to fill out -
• Name:
• Phone Number:
• Address:
• E-mail:
• Painting project description:
• And my info to:
• My phone number: (555) 318-7046
• My web address bluefinchpainting.example
Nice to have
• My logo that was designed here on ArtHatch

```html
<!DOCTYPE html>
<html lang="en">
<head>
<meta charset="utf-8">
<title>Bluefinch Painting</title>
<link href="https://fonts.googleapis.com/css2?family=Open+Sans:wght@400;600;700&family=Roboto+Condensed:wght@700&family=Varela+Round&display=swap" rel="stylesheet">
<style>
  :root {
    --blue: #0c57a9;
    --blue-dark: #0a4a92;
    --navy: #26344e;
    --yellow: #f8c62b;
    --orange: #f07d1a;
    --gray-bg: #d5d7db;
    --text: #333;
    --white: #fff;
  }
  * { box-sizing: border-box; margin: 0; padding: 0; }
  html, body { width: 814px; height: 1200px; overflow: hidden; }
  body { position: relative; font-family: "Open Sans", Arial, sans-serif; color: var(--text); background: var(--gray-bg); }
  .abs { position: absolute; }

  .topbar { top: 0; left: 0; width: 814px; height: 33px; background: var(--white); }
  .brand { left: 118px; top: 5px; display: flex; align-items: center; gap: 6px; font-weight: 700; font-size: 16px; color: var(--navy); letter-spacing: .5px; white-space: nowrap; }
  .brand .mark { width: 18px; height: 18px; background: var(--blue); }
  .top-phone { left: 548px; top: 6px; font-size: 15px; font-weight: 600; color: var(--orange); display: flex; align-items: center; gap: 6px; white-space: nowrap; }

  .nav { top: 33px; left: 0; width: 528px; height: 40px; background: var(--blue); }
  .nav a { position: absolute; top: 13px; font-family: "Roboto Condensed", sans-serif; font-weight: 700; font-size: 11px; line-height: 14px; color: var(--white); text-decoration: none; white-space: nowrap; }
  .nav a.active { top: 9px; padding: 4px 7px; background: #0d4b8d; border: 1px solid #3a78c0; }
  .quote { top: 33px; left: 528px; width: 286px; height: 40px; background: var(--yellow); display: flex; align-items: center; gap: 10px; padding-left: 20px; font-family: "Roboto Condensed", sans-serif; font-weight: 700; font-size: 11px; color: var(--navy); white-space: nowrap; }

  .hero { top: 73px; left: 0; width: 814px; height: 300px; background: linear-gradient(180deg, #8fbde8 0%, #b9cfe0 22%, #8e8676 45%, #5f7a3e 70%, #4e6b33 85%, #8b8f8c 100%); }
  .quick { top: 372px; left: 0; width: 814px; height: 61px; background: rgba(20, 95, 175, .92); }
  .quick h3 { position: absolute; left: 129px; top: 4px; font-family: "Varela Round", sans-serif; font-size: 12px; font-weight: 400; color: var(--white); }
  .quick form { position: absolute; left: 127px; top: 25px; display: flex; gap: 6px; }
  .quick input { height: 18px; border: none; background: #d5dbe4; font-family: "Open Sans", sans-serif; font-size: 9px; padding: 0 6px; color: #555; }
  .quick button { height: 18px; padding: 0 6px; font-family: "Open Sans", sans-serif; font-size: 9px; background: #e6e6e6; border: 1px solid #aaa; margin-left: 2px; }

  .bg-photo { top: 433px; left: 0; width: 470px; height: 280px; background: radial-gradient(ellipse at 35% 55%, rgba(255,255,255,.45), rgba(213,215,219,0) 70%); }

  .welcome { top: 441px; left: 0; width: 814px; text-align: center; }
  .welcome h2 { font-family: "Varela Round", sans-serif; font-weight: 400; font-size: 12px; color: #222; }
  .rule { width: 188px; height: 3px; margin: 5px auto 0; border-top: 1px solid #999; border-bottom: 1px solid #999; }
  .welcome .lead { margin-top: 16px; font-size: 7px; font-weight: 700; color: #222; }
  .welcome .body { margin: 10px auto 0; width: 570px; font-size: 7.5px; line-height: 10px; color: var(--text); }
  .welcome .more { display: block; margin-top: 5px; font-size: 8.5px; color: #222; }

  .dash { left: 0; width: 814px; border-top: 1px dashed #a8abb0; }
  .label { left: 0; width: 814px; text-align: center; }
  .label span { display: inline-block; background: var(--blue); color: var(--white); font-family: "Varela Round", sans-serif; font-size: 11px; padding: 1px 6px; }
  .label .rule { width: 218px; margin-top: 4px; }

  .service { top: 610px; width: 150px; }
  .service svg { display: block; height: 60px; margin-left: 10px; }
  .service h4 { margin-top: 9px; font-size: 8px; font-weight: 700; text-align: center; width: 95px; color: #222; }
  .service h4.hl { color: var(--blue); }
  .service p { margin-top: 2px; width: 100px; font-size: 7.5px; line-height: 10px; color: var(--text); }

  .project { top: 835px; width: 140px; }
  .project .photo { width: 136px; height: 134px; }
  .project h5 { margin-top: 10px; font-size: 7.5px; font-weight: 600; color: var(--blue); text-align: center; }
  .project p { margin-top: 5px; font-size: 7.5px; line-height: 10px; color: var(--text); }

  .foot-bar { top: 1065px; left: 0; width: 814px; height: 23px; background: var(--navy); }
  .foot-bar h6 { position: absolute; top: 5px; font-size: 10px; font-weight: 600; color: var(--white); white-space: nowrap; }
  .foot { top: 1088px; left: 0; width: 814px; height: 92px; background: var(--blue); color: var(--white); font-size: 7.5px; }
  .links { left: 123px; top: 10px; line-height: 15.5px; }
  .contact { left: 231px; top: 10px; width: 140px; }
  .contact div { display: flex; gap: 8px; align-items: flex-start; margin-bottom: 6px; white-space: nowrap; }
  .contact svg { flex: none; }
  .contact .mail { font-size: 6.5px; }
  .news { left: 375px; top: 9px; width: 140px; }
  .news input { margin-top: 10px; width: 133px; height: 19px; border: none; font-size: 7.5px; padding: 0 4px; }
  .news button { margin-top: 6px; background: var(--navy); color: var(--white); border: none; font-size: 8px; padding: 4px 10px; }
  .foot-brand { left: 520px; top: 20px; display: flex; align-items: center; gap: 6px; font-size: 15px; font-weight: 700; color: #9bb8da; letter-spacing: .5px; white-space: nowrap; }
  .foot-brand .mark { width: 18px; height: 18px; background: #9bb8da; }
  .social { left: 572px; top: 64px; display: flex; gap: 4px; }
  .social span { width: 18px; height: 18px; border: 1.5px solid #c9d8ec; border-radius: 50%; }
  .copy { top: 1180px; left: 0; width: 814px; height: 20px; background: var(--blue-dark); color: var(--white); text-align: center; font-size: 7.5px; line-height: 20px; }
  .copy b { font-weight: 700; }
</style>
</head>
<body>

<header>
  <div class="abs topbar"></div>
  <div class="abs brand"><span class="mark"></span>Bluefinch Painting</div>
  <div class="abs top-phone">
    <svg width="13" height="13" viewBox="0 0 24 24"><circle cx="12" cy="12" r="11" fill="none" stroke="#1f6cc0" stroke-width="2"/><path d="M8 6l2 0 1 3-1.5 1a7 7 0 0 0 4.5 4.5L15 13l3 1v2a2 2 0 0 1-2 2A10 10 0 0 1 6 8a2 2 0 0 1 2-2z" fill="#1f6cc0"/></svg>
    (555) 318-7046
  </div>
  <nav class="abs nav">
    <a class="active" href="#" style="left:122px">HOME</a>
    <a href="#" style="left:183px">ABOUT US</a>
    <a href="#" style="left:259px">SERVICES</a>
    <a href="#" style="left:334px">PROJECTS</a>
    <a href="#" style="left:411px">FAQ</a>
    <a href="#" style="left:462px">CONTACT US</a>
  </nav>
  <div class="abs quote">GET A FREE QUOTE
    <svg width="20" height="20" viewBox="0 0 24 24"><rect x="3" y="5" width="15" height="16" rx="2" fill="none" stroke="#1a5fb0" stroke-width="2.2"/><path d="M10 14l9-9 2.5 2.5-9 9H10z" fill="#1a5fb0"/></svg>
  </div>
</header>

<section>
  <div class="abs hero" role="img" aria-label="Photo of a two-storey beige house with a garden of flowering shrubs"></div>
  <div class="abs quick">
    <h3>Quick Contact with us</h3>
    <form>
      <input style="width:87px" placeholder="Name">
      <input style="width:86px" placeholder="Mobile">
      <input style="width:115px" placeholder="Email">
      <input style="width:199px" placeholder="Message">
      <button type="button">SUBMIT</button>
    </form>
  </div>
</section>

<main>
  <div class="abs bg-photo" role="img" aria-label="Faded photo of a company truck and van parked by a house"></div>

  <div class="abs welcome">
    <h2>Welcome to Bluefinch Painting</h2>
    <div class="rule"></div>
    <p class="lead">LOREM IPSUM DOLOR SIT AMET, CONSEC TESDFGDIR ADIPISCING. PRSENT VESTIBULUM MOLEDFGSFD STIE LACUICING. PRSENT VESTIBUIRHS. AENEON.</p>
    <p class="body">Lorem ipsum dolor sit amet, consec tfhketuer adip iscing. Praesent vestibu lum molestie lacgfhjuiirhs. Lorem ipsum dolor sit amet, consec tfhketuer adip iscing. Praesent vestibu lum molestie lacgfhjuiirhs. Aenean non ummy hendreriauris. Phasellus. porta. Fusce suscipit varius mium sofhjfgjh ghfdgsfd dfjciis totdnatibus et magis dis parturie. Aenean non ummy hendreriauris. Phasellus. porta. Fusce suscipit varius mium sofhjfgjh ghfdgsfd dfjciis totdnatibus et magis dis parturie.</p>
    <span class="more">More &gt;&gt;</span>
  </div>

  <div class="abs dash" style="top:557px"></div>
  <div class="abs label" style="top:567px"><span>Our Services</span><div class="rule"></div></div>

  <div class="abs service" style="left:124px">
    <svg width="80" height="60" viewBox="0 0 80 60"><path d="M4 30L38 2l34 28h-9v28H13V30z" fill="var(--blue)"/><rect x="30" y="38" width="14" height="20" fill="var(--gray-bg)"/><rect x="50" y="24" width="6" height="22" transform="rotate(-45 53 35)" fill="#555"/></svg>
    <h4 class="hl">EXTERIOR</h4>
    <p>Neque porro quisquam est, qui dolorem ipsum adafquia dolor sit amet, consectetur, adipiscfffi velit, sed quia non numquam eius porro qufgh dffdisquam est,</p>
  </div>
  <div class="abs service" style="left:280px">
    <svg width="80" height="60" viewBox="0 0 80 60"><path d="M18 22h24v16H18z M12 28h6v20h-6z M42 28h6v20h-6z M12 42h36v8H12z" fill="#555"/><path d="M58 12h12l-3 10h-6z" fill="#555"/><rect x="63" y="22" width="2" height="34" fill="#555"/><rect x="56" y="55" width="16" height="2" fill="#555"/></svg>
    <h4>INTERIOR</h4>
    <p>Neque porro quisquam est, qui dolorem ipsum adafquia dolor sit amet, consectetur, adipiscfffi velit, sed quia non numquam eius porro qufgh dffdisquam est,</p>
  </div>
  <div class="abs service" style="left:438px">
    <svg width="80" height="60" viewBox="0 0 80 60"><path d="M12 22L40 2l28 20v36H12z" fill="#555"/><g fill="var(--gray-bg)"><rect x="20" y="26" width="8" height="7"/><rect x="36" y="26" width="8" height="7"/><rect x="52" y="26" width="8" height="7"/><rect x="20" y="40" width="8" height="7"/><rect x="52" y="40" width="8" height="7"/><rect x="35" y="42" width="10" height="16"/></g></svg>
    <h4>RESIDENTIAL</h4>
    <p>Neque porro quisquam est, qui dolorem ipsum adafquia dolor sit amet, consectetur, adipiscfffi velit, sed quia non numquam eius porro qufgh dffdisquam est,</p>
  </div>
  <div class="abs service" style="left:585px">
    <svg width="80" height="60" viewBox="0 0 80 60"><rect x="6" y="18" width="26" height="40" fill="#555"/><rect x="30" y="2" width="32" height="56" fill="#555"/><g fill="var(--gray-bg)"><rect x="12" y="24" width="5" height="5"/><rect x="21" y="24" width="5" height="5"/><rect x="12" y="36" width="5" height="5"/><rect x="21" y="36" width="5" height="5"/><rect x="37" y="9" width="6" height="6"/><rect x="49" y="9" width="6" height="6"/><rect x="37" y="22" width="6" height="6"/><rect x="49" y="22" width="6" height="6"/><rect x="37" y="35" width="6" height="6"/><rect x="49" y="35" width="6" height="6"/></g></svg>
    <h4>COMMERCIAL</h4>
    <p>Neque porro quisquam est, qui dolorem ipsum adafquia dolor sit amet, consectetur, adipiscfffi velit, sed quia non numquam eius porro qufgh dffdisquam est,</p>
  </div>

  <div class="abs dash" style="top:773px"></div>
  <div class="abs label" style="top:784px"><span>Our Projects</span><div class="rule"></div></div>

  <svg class="abs" style="left:116px;top:884px" width="26" height="40" viewBox="0 0 26 40"><path d="M20 4L6 20l14 16" fill="none" stroke="var(--blue)" stroke-width="6"/></svg>
  <svg class="abs" style="left:672px;top:884px" width="26" height="40" viewBox="0 0 26 40"><path d="M6 4l14 16L6 36" fill="none" stroke="#555" stroke-width="6"/></svg>

  <div class="abs project" style="left:170px">
    <div class="photo" role="img" aria-label="Project photo: painted two-storey house with a patio" style="background:linear-gradient(180deg,#c9d3dc,#8c8a80 55%,#6d7a52)"></div>
    <h5>Lorem ipsum dolor sit</h5>
    <p>Lorem ipsum dolor sit amet, consec tfhketuer adip iscing. Praesent vestibu lum molestie lacgfhjuiirhs. aderLorem ipsum dolor sit amet, consec tfhketuer adip iscing. Praesent aersvvestibu lum molestie lacgfhjuiirhs.</p>
  </div>
  <div class="abs project" style="left:338px">
    <div class="photo" role="img" aria-label="Project photo: house front with lawn and lamp post" style="background:linear-gradient(180deg,#dfe4e8,#6f7a62 45%,#7f8d5d 70%,#a9a9a2)"></div>
    <h5>Lorem ipsum dolor sit</h5>
    <p>Lorem ipsum dolor sit amet, consec tfhketuer adip iscing. Praesent vestibu lum molestie lacgfhjuiirhs. aderLorem ipsum dolor sit amet, consec tfhketuer adip iscing. Praesent aersvvestibu lum molestie lacgfhjuiirhs.</p>
  </div>
  <div class="abs project" style="left:508px">
    <div class="photo" role="img" aria-label="Project photo: house entrance with stone column and pink flowers" style="background:linear-gradient(180deg,#d9dde0,#a09682 45%,#6f7d4a 75%,#c5567a)"></div>
    <h5>Lorem ipsum dolor sit</h5>
    <p>Lorem ipsum dolor sit amet, consec tfhketuer adip iscing. Praesent vestibu lum molestie lacgfhjuiirhs. aderLorem ipsum dolor sit amet, consec tfhketuer adip iscing. Praesent aersvvestibu lum molestie lacgfhjuiirhs.</p>
  </div>
</main>

<footer>
  <div class="abs foot-bar">
    <h6 style="left:123px">QUICK LINKS</h6>
    <h6 style="left:231px">CONTACT INFO</h6>
    <h6 style="left:375px">GET NEWS UPDATES</h6>
  </div>
  <div class="abs foot">
    <div class="abs links">Home<br>About Us<br>Services<br>Projects<br>Contact Us</div>
    <div class="abs contact">
      <div><svg width="10" height="12" viewBox="0 0 10 12"><path d="M5 0a4 4 0 0 1 4 4c0 3-4 8-4 8S1 7 1 4a4 4 0 0 1 4-4z" fill="#1d2c45"/></svg><span>Lorem ipsum dofglor sit<br>amet, consec tetuer.</span></div>
      <div><svg width="10" height="10" viewBox="0 0 10 10"><circle cx="5" cy="5" r="5" fill="#1d2c45"/></svg><span>(555) 318-7046</span></div>
      <div><svg width="10" height="10" viewBox="0 0 10 10"><rect x="0" y="3" width="10" height="6" fill="#1d2c45"/><rect x="2" y="0" width="6" height="3" fill="#1d2c45"/></svg><span>012-345-6789</span></div>
      <div><svg width="10" height="8" viewBox="0 0 10 8"><rect width="10" height="8" fill="#1d2c45"/><path d="M0 0l5 4 5-4" fill="none" stroke="#6f8fbf"/></svg><span class="mail">support@bluefinchpainting.example</span></div>
    </div>
    <div class="abs news">
      Lorem ipsum dolor sit amet, consec tetuer adipiscing elit.
      <input placeholder="Your E-mail">
      <button type="button">SUBMIT</button>
    </div>
    <div class="abs foot-brand"><span class="mark"></span>Bluefinch Painting</div>
    <div class="abs social"><span></span><span></span><span></span><span></span></div>
  </div>
  <div class="abs copy">© 2015. <b>Bluefinch Painting.</b> All rights reserved.</div>
</footer>

</body>
</html>
```